New Alcoholic Spiked Seltzer Line

We need a can design for a line of low calorie alcoholic seltzer. This product is a sparkling water and vodka drink with no sugar added in a slim 12 oz can.

This is a lighter, healthier, alternative to the sugary ready-to-drinks on the market. The product contains only 3 ingredients: Vodka, Water and Natural Flavors. It has only 100 calories but still has 5% alcohol, so you don't need to sacrifice alcohol to cut calories.

This product also does not contain any preservatives.

We want this design to communicate the following objectives to the consumer and in this order:

1. Appetizing product
2.Low calorie
3.Communicate the type of beverage (Spiked Seltzer)

The brand name of the product is VELKA.

The flavor of the product needed to be used for the design is Mango-Orange.

Comparable products are:

www.brindlefizzworks.example/
https://www.quorvabubbles.example
https://pelnavo.example/

The designs should not infringe or copy the creative directions of the products mentionned above. They are only given so that you can better understand the type of product we are developing.

Target Market(s)

Young Professional women between the ages of 25 and 44

Industry/Entity Type

Product

Colors

Designer to choose colors to be used in the design.

Requirements
Must have
• Design extendibility, meaning it can be adapted for other flavors.
• This is a new category in the market we are targeting, so consumers must easily be able to identify what type of product this is.

```html
<!DOCTYPE html>
<html lang="en">
<head>
<meta charset="utf-8">
<title>VELKA Spiked Seltzer – Mango Orange Can Label</title>
<link rel="stylesheet" href="https://fonts.googleapis.com/css2?family=Source+Sans+3:wght@400;500;700&display=swap">
<style>
  :root {
    --page: #ffffff;
    --silver-light: #e6e7e9;
    --silver-mid: #c9cbce;
    --silver-dark: #a9acb0;
    --ink: #2b2b2d;
    --wine: #7a0f17;
    --crimson: #c8233e;
    --berry: #b01e48;
    --grey-text: #4a4a4c;
    --mango: #f5a10f;
    --mango-deep: #e8900a;
    --badge-text: #ffffff;
    --band: #232325;
    --band-text: #f6a623;
  }
  * { margin: 0; padding: 0; box-sizing: border-box; }
  html, body {
    width: 1200px;
    height: 2546px;
    overflow: hidden;
    background: var(--page);
  }
  .canvas {
    position: relative;
    width: 1200px;
    height: 2546px;
    font-family: "Source Sans 3", "Myriad Pro", Arial, sans-serif;
  }
  .label {
    position: absolute;
    left: 140px;
    top: 116px;
    width: 836px;
    height: 2342px;
    border-radius: 36px;
    overflow: hidden;
    background: linear-gradient(90deg, var(--silver-dark) 0%, var(--silver-light) 22%, var(--silver-light) 55%, var(--silver-mid) 85%, var(--silver-dark) 100%);
  }
  .product-type {
    position: absolute;
    left: 0;
    top: 395px;
    width: 398px;
    text-align: right;
  }
  .product-type__name {
    font-weight: 400;
    font-size: 90px;
    line-height: 83px;
    color: var(--wine);
  }
  .product-type__tagline {
    margin-top: 10px;
    font-size: 43px;
    line-height: 58px;
    color: var(--crimson);
  }
  .product-type__ingredients {
    margin-top: 8px;
    font-size: 43px;
    line-height: 55px;
    color: var(--grey-text);
  }
  .accent-bar {
    position: absolute;
    left: 108px;
    top: 844px;
    width: 287px;
    height: 45px;
    background: var(--berry);
  }
  .mascot-area {
    position: absolute;
    left: 0;
    top: 895px;
    width: 430px;
    height: 740px;
    background: radial-gradient(ellipse at 40% 45%, rgba(80,82,86,0.45) 0%, rgba(150,152,156,0.25) 55%, rgba(200,202,205,0) 80%);
  }
  .brand-name {
    position: absolute;
    left: 625px;
    top: 1090px;
    transform-origin: center;
    transform: translate(-50%, -50%) rotate(-90deg);
    font-weight: 400;
    font-size: 495px;
    line-height: 1;
    letter-spacing: 10px;
    color: var(--ink);
    white-space: nowrap;
  }
  .flavor-badge {
    position: absolute;
    left: 76px;
    top: 1606px;
    width: 330px;
    height: 330px;
    border-radius: 50%;
    background: radial-gradient(circle at 40% 40%, var(--mango) 0%, var(--mango-deep) 100%);
    display: flex;
    flex-direction: column;
    align-items: center;
    justify-content: center;
    transform: rotate(-10deg);
  }
  .flavor-badge__name {
    font-weight: 700;
    font-size: 62px;
    line-height: 66px;
    color: var(--badge-text);
    text-align: center;
  }
  .stats-band {
    position: absolute;
    left: 0;
    top: 1936px;
    width: 100%;
    height: 406px;
    background: var(--band);
    display: flex;
    justify-content: center;
    padding-top: 68px;
  }
  .stats-band__text {
    font-size: 49px;
    font-weight: 500;
    line-height: 60px;
    color: var(--band-text);
    letter-spacing: 0.5px;
  }
</style>
</head>
<body>
  <main class="canvas">
    <section class="label" aria-label="VELKA Spiked Seltzer can label, mango orange flavor">
      <div class="mascot-area" role="img" aria-label="Large cropped brand mascot artwork in dark grey line art"></div>

      <div class="product-type">
        <h1 class="product-type__name">Spiked<br>Seltzer</h1>
        <p class="product-type__tagline">low calorie<br>alcoholic seltzer</p>
        <p class="product-type__ingredients">vodka, water &amp;<br>natural flavors</p>
      </div>
      <div class="accent-bar"></div>

      <div class="brand-name">VELKA</div>

      <div class="flavor-badge" role="img" aria-label="Orange brush-textured flavor circle: mango orange">
        <p class="flavor-badge__name">mango<br>orange</p>
      </div>

      <div class="stats-band">
        <p class="stats-band__text">5% alcohol - 100 calories</p>
      </div>
    </section>
  </main>
</body>
</html>
```